Lumbra Ember Oven Kitchen (restaurant)

Restaurant with a cool vibe.
We need a refresh of existing site. Appealing to a hip crowd of 25 or older age bracket (mid price to high small town). Constant changes food and cocktail menu. A vibing atmosphere with jazz funk hip music.
Must be able to scale for any device… phone/mobile device super important.
Instagram: @Lumbra.Bexwell
Website: lumbrabexwell.example

Target Market(s)

25-55 age group

Number of Pages Required

1 page

Font styles to use
Sans Serif

Requirements
Must have
• Simple to navigate. Simplicity is the key to all sophistication.

Links/Buttons
Menu
Gift Cards
Reservations
Take Out
Contact Us
Should not have
• Please, nothing generic looking… no cookie cutter look. Originality

```html
<!DOCTYPE html>
<html lang="en">
<head>
<meta charset="utf-8">
<title>Lumbra Ember Oven Kitchen</title>
<link href="https://fonts.googleapis.com/css2?family=Oswald:wght@400;500;600&family=Lato:ital,wght@0,400;0,700;1,400&display=swap" rel="stylesheet">
<style>
:root{
  --black:#000;
  --panel:#0c0d10;
  --panel-2:#111216;
  --red:#ec1c24;
  --white:#fff;
  --muted:#d6d6d6;
  --gold-1:#d9984a;
  --gold-2:#8a4f17;
  --card:#151517;
}
*{box-sizing:border-box;margin:0;padding:0}
html,body{width:1200px;height:3699px;overflow:hidden;background:var(--black)}
body{position:relative;font-family:'Lato',sans-serif;color:var(--white)}
.abs{position:absolute}
.display{font-family:'Oswald',sans-serif;text-transform:uppercase;font-weight:500}

/* header & hero */
.hero{left:0;top:0;width:1200px;height:628px;background:linear-gradient(180deg,#2f3440 0%,#4a3a33 35%,#5a3a2c 60%,#1c1a1a 100%)}
.brand{left:118px;top:22px;width:220px}
.brand-name{font-family:'Lato',sans-serif;font-weight:700;font-size:42px;letter-spacing:3px;line-height:1}
.brand-sub{font-family:'Lato',sans-serif;font-weight:700;font-size:15px;margin-left:22px;margin-top:2px}
.nav{top:42px;left:370px;display:flex;gap:31px;font-size:16px;font-weight:400}
.nav a{color:var(--white);text-decoration:none}
.hero-title{left:611px;top:236px;font-size:64px;line-height:68px;font-weight:600}
.btn{display:flex;align-items:center;justify-content:center;font-size:16px;font-weight:700;text-transform:uppercase;color:var(--white);border-radius:3px}
.btn-outline{border:1.5px solid var(--white)}
.btn-red{background:var(--red)}
.btn-red-outline{border:1.5px solid var(--red);color:var(--red);font-weight:400}

/* about */
.about-panel{left:498px;top:564px;width:593px;height:413px;background:var(--panel)}
.about-frame{left:95px;top:624px;width:490px;height:335px;border:2px solid var(--red)}
.about-photo{left:112px;top:606px;width:491px;height:337px;background:linear-gradient(135deg,#5b3a26,#2a1d17 60%,#3b2a22)}
.section-title{font-size:38px;font-weight:500}
.rule{height:2px;background:var(--red)}
.about-text{left:660px;top:672px;width:400px;font-size:13px;line-height:25px;color:var(--muted)}
.about-text p+p{margin-top:7px}

/* menu */
.menu-bg{left:0;top:977px;width:1200px;height:601px;background:linear-gradient(180deg,#0e0e0e,#181818 50%,#0d0d0d)}
.dish-frame{width:300px;height:199px;border:2px solid var(--red);border-top:none;border-right:none}
.dish-frame::before{content:"";position:absolute;left:0;top:0;width:12px;height:2px;background:var(--red)}
.dish-photo{width:300px;height:201px}
.dish-label{width:300px;text-align:center;font-size:20px;font-weight:700;text-transform:uppercase}

/* reservation */
.res-panel{left:187px;top:1589px;width:826px;height:401px;background:var(--panel)}
.res-box{left:217px;top:1645px;width:765px;height:272px;border:1px solid #cfcfcf}
.res-title{left:500px;top:1624px;width:200px;text-align:center;background:var(--panel);font-family:'Oswald',sans-serif;font-weight:400;font-size:36px;line-height:48px;text-transform:uppercase}
.field-label{font-size:12px;text-transform:uppercase}
.field{width:217px;height:40px;border:1px solid #cfcfcf;font-size:13px;padding:12px 12px;color:var(--white)}
.stat{width:120px;text-align:center}
.stat b{display:block;font-size:21px;font-weight:400}
.stat span{font-size:12px;text-transform:uppercase}
.stat-divider{width:1px;height:50px;background:#555}

/* gift cards */
.gift-bg{left:0;top:1990px;width:1200px;height:481px;background:radial-gradient(ellipse at 20% 40%,#3a3226 0%,#1a1814 45%,#0b0b0b 100%)}
.gift-text{left:112px;top:2125px;width:955px;font-size:15px;line-height:25px}
.gift-card{width:296px;height:168px;border-radius:14px;overflow:hidden;
  background:
    radial-gradient(ellipse 70px 45px at 50px 35px,rgba(217,152,74,.55),transparent),
    linear-gradient(180deg,var(--card) 0%,var(--card) 64%,var(--gold-1) 72%,var(--gold-2) 80%,var(--card) 88%,var(--card) 100%)}
.gift-head{left:92px;top:26px;font-family:'Oswald',sans-serif;font-size:16px;font-weight:500}
.gift-off{left:96px;top:52px;font-size:30px;line-height:28px}
.gift-code{left:178px;top:69px;width:98px;height:32px;border:1px dashed var(--white);font-size:16px;display:flex;align-items:center;justify-content:center}

/* testimonials */
.quote-card{width:381px;height:175px;background:var(--panel-2)}
.avatar-frame{width:79px;height:79px;border:1.5px solid var(--white);border-top:none;border-right:none}
.avatar{width:79px;height:79px;background:linear-gradient(135deg,#7a8da0,#3c4a57)}
.quote-mark{font-family:'Oswald',sans-serif;color:var(--red);font-size:40px;line-height:1}
.quote-text{width:316px;font-size:12px;line-height:26px;font-style:italic}
.quote-name{font-size:15px;font-weight:700}

/* map & contact */
.map{left:0;top:2893px;width:1200px;height:439px;background:linear-gradient(135deg,#9a9a9a,#7e7e7e 55%,#8e8e8e)}
.contact-bar{left:0;top:3332px;width:1200px;height:88px;background:var(--red)}
.contact-item{display:flex;align-items:center;gap:10px;font-size:16px}

/* footer */
.foot-col h4{font-family:'Oswald',sans-serif;font-size:19px;font-weight:500;margin-bottom:8px}
.foot-col p{font-size:15px;line-height:26.5px}
.foot-rule{left:112px;top:3641px;width:979px;height:1px;background:#333}
.copyright{left:0;top:3661px;width:1200px;text-align:center;font-size:15px}
</style>
</head>
<body>

<!-- HERO -->
<div class="abs hero" role="img" aria-label="Evening street photo of the red brick restaurant building with traffic lights"></div>
<div class="abs brand">
  <div class="brand-name">LUMBRA</div>
  <div class="brand-sub">Ember Oven Kitchen</div>
</div>
<nav class="abs nav">
  <a href="#gift">GIFT CARDS</a><a href="#menu">MENU</a><a href="#contact">CONTACT US</a><a href="#reservation">RESERVATIONS</a><a href="#menu">ORDER ONLINE</a><a href="#menu">TAKE OUT</a>
</nav>
<h1 class="abs display hero-title">Dinner ideas?<br>How about Lumbra!</h1>
<a class="abs btn btn-outline" style="left:611px;top:395px;width:162px;height:51px">Contact us</a>
<a class="abs btn btn-red" style="left:788px;top:395px;width:232px;height:51px">Make a reservation</a>

<!-- ABOUT -->
<div class="abs about-panel"></div>
<div class="abs about-frame"></div>
<div class="abs about-photo" role="img" aria-label="Photo of the restaurant team smiling by the wood fired oven"></div>
<div class="abs rule" style="left:660px;top:637px;width:43px"></div>
<h2 class="abs display section-title" style="left:710px;top:612px">About us</h2>
<div class="abs about-text">
  <p>Lorem ipsum dolor sit amet, consectetur adipiscing elkjlit, sed do eiusmod tempor incididunt ut labore et dolore magna aliqua. Quis ipsum suspendisse ultrices gravida. Risus commiverra maecenas accumsan lacus vel facilisis.</p>
  <p>Lorem ipsum dolor sit amet, consectetur adipiscing elkjlit, sed do eiusmod tempor incididunt ut labore et dolore magna aliqua. Quis ipsum suspendisse ultrices gravida</p>
</div>
<a class="abs btn btn-red-outline" style="left:657px;top:874px;width:147px;height:43px">Learn more</a>

<!-- MENU -->
<div class="abs menu-bg" role="img" aria-label="Dim photo of the dining room interior"></div>
<h2 class="abs display section-title" style="left:0;top:1052px;width:1200px;text-align:center">Our menu's</h2>
<a class="abs btn btn-red" style="left:456px;top:1112px;width:138px;height:45px;font-weight:400">Dinner</a>
<a class="abs btn btn-outline" style="left:606px;top:1112px;width:137px;height:45px;font-weight:400">Takeout</a>

<div class="abs dish-frame" style="left:112px;top:1194px"></div>
<div class="abs dish-photo" style="left:125px;top:1184px;background:linear-gradient(135deg,#d8d2c0,#4d5a2a 55%,#2a3a18)" role="img" aria-label="Photo of grilled flatbread with greens"></div>
<div class="abs dish-label" style="left:125px;top:1405px">Shareables</div>

<div class="abs dish-frame" style="left:443px;top:1194px"></div>
<div class="abs dish-photo" style="left:455px;top:1184px;background:linear-gradient(135deg,#c9823a,#b3452a 50%,#5a7a2a)" role="img" aria-label="Photo of wood fired pizza with arugula"></div>
<div class="abs dish-label" style="left:455px;top:1405px">Wood fired pizza</div>

<div class="abs dish-frame" style="left:775px;top:1194px"></div>
<div class="abs dish-photo" style="left:786px;top:1184px;background:linear-gradient(135deg,#e8e4da,#b89a5a 50%,#6a5a30)" role="img" aria-label="Photo of rolled pork sandwich plate"></div>
<div class="abs dish-label" style="left:786px;top:1405px">Sandwiches</div>

<a class="abs btn btn-red-outline" style="left:518px;top:1457px;width:164px;height:43px">View all menu</a>

<!-- RESERVATION -->
<div class="abs res-panel"></div>
<div class="abs res-box"></div>
<h2 class="abs res-title">Reservation</h2>
<div class="abs field-label" style="left:251px;top:1707px">Full name</div>
<div class="abs field-label" style="left:491px;top:1707px">Email address</div>
<div class="abs field-label" style="left:730px;top:1707px">Phone number</div>
<div class="abs field" style="left:251px;top:1728px">Jonathan Doe</div>
<div class="abs field" style="left:491px;top:1728px">Joe@do</div>
<div class="abs field" style="left:730px;top:1728px">Number</div>
<div class="abs stat" style="left:415px;top:1802px"><b>5</b><span>Guests</span></div>
<div class="abs stat-divider" style="left:531px;top:1807px"></div>
<div class="abs stat" style="left:538px;top:1802px"><b>12 JUNE</b><span>Date</span></div>
<div class="abs stat-divider" style="left:667px;top:1807px"></div>
<div class="abs stat" style="left:663px;top:1802px"><b>19:00</b><span>Time</span></div>
<a class="abs btn btn-red" style="left:453px;top:1891px;width:293px;height:51px">Send reservation request</a>

<!-- GIFT CARDS -->
<div class="abs gift-bg" role="img" aria-label="Dark overhead photo of plated dishes"></div>
<div class="abs rule" style="left:112px;top:2091px;width:42px"></div>
<h2 class="abs display section-title" style="left:162px;top:2066px">Gift cards</h2>
<p class="abs gift-text">Lorem ipsum dolor sit amet, consectetur adipiscing elkjlit, sed do eiusmod tempor incididunt ut laborere magna aliqua. Quis ipsum suspendisse ultrices gravida. Risus commiverra maecenas accumsan lacus vel facilisis.</p>

<div class="abs gift-card" style="left:135px;top:2217px" role="img" aria-label="Gift card with gold ribbon and bow">
  <div class="abs gift-head">THE STANDARD LOREM IPSUM</div>
  <div class="abs gift-off">20%<br>OFF</div>
  <div class="abs gift-code">ABCD1234</div>
</div>
<div class="abs gift-card" style="left:463px;top:2217px" role="img" aria-label="Gift card with gold ribbon and bow">
  <div class="abs gift-head">THE STANDARD LOREM IPSUM</div>
  <div class="abs gift-off">20%<br>OFF</div>
  <div class="abs gift-code">ABCD1234</div>
</div>
<div class="abs gift-card" style="left:791px;top:2217px" role="img" aria-label="Gift card with gold ribbon and bow">
  <div class="abs gift-head">THE STANDARD LOREM IPSUM</div>
  <div class="abs gift-off">20%<br>OFF</div>
  <div class="abs gift-code">ABCD1234</div>
</div>

<!-- TESTIMONIALS -->
<h2 class="abs display section-title" style="left:0;top:2544px;width:1200px;text-align:center">What they say about us</h2>
<svg class="abs" style="left:110px;top:2704px" width="30" height="20" viewBox="0 0 30 20"><path d="M29 10H2M10 2L2 10l8 8" fill="none" stroke="#fff" stroke-width="1.5"/></svg>
<svg class="abs" style="left:1066px;top:2704px" width="30" height="20" viewBox="0 0 30 20"><path d="M1 10h27M20 2l8 8-8 8" fill="none" stroke="#fff" stroke-width="1.5"/></svg>

<div class="abs quote-card" style="left:197px;top:2633px"></div>
<div class="abs avatar-frame" style="left:148px;top:2686px"></div>
<div class="abs avatar" style="left:155px;top:2679px" role="img" aria-label="Guest portrait"></div>
<div class="abs quote-mark" style="left:258px;top:2652px">“</div>
<p class="abs quote-text" style="left:284px;top:2650px">Lorem ipsum dolor sit amet, consectetur adipiscing elit, sed do eiusmod tempor incididunt ut labore et dolore magna aliqua. Quis ipsususpendisse ultrices gravida. Risus commodo</p>
<div class="abs rule" style="left:291px;top:2777px;width:24px"></div>
<div class="abs quote-name" style="left:322px;top:2767px">John Smith</div>

<div class="abs quote-card" style="left:669px;top:2633px"></div>
<div class="abs avatar-frame" style="left:621px;top:2686px"></div>
<div class="abs avatar" style="left:628px;top:2679px" role="img" aria-label="Guest portrait"></div>
<div class="abs quote-mark" style="left:731px;top:2652px">“</div>
<p class="abs quote-text" style="left:757px;top:2650px">Lorem ipsum dolor sit amet, consectetur adipiscing elit, sed do eiusmod tempor incididunt ut labore et dolore magna aliqua. Quis ipsususpendisse ultrices gravida. Risus commodo</p>
<div class="abs rule" style="left:764px;top:2777px;width:24px"></div>
<div class="abs quote-name" style="left:795px;top:2767px">John Smith</div>

<!-- MAP -->
<div class="abs map" role="img" aria-label="Street map of downtown Bexwell showing the restaurant location"></div>
<svg class="abs" style="left:676px;top:3078px" width="22" height="30" viewBox="0 0 22 30"><path d="M11 29C11 29 1 17 1 11a10 10 0 0 1 20 0c0 6-10 18-10 18z" fill="#ec1c24"/><circle cx="11" cy="11" r="4" fill="#fff"/></svg>

<!-- CONTACT BAR -->
<div class="abs contact-bar" id="contact"></div>
<div class="abs contact-item" style="left:235px;top:3362px">
  <svg width="30" height="30" viewBox="0 0 30 30"><path d="M15 22s-7-8-7-12a7 7 0 0 1 14 0c0 4-7 12-7 12z" fill="none" stroke="#fff" stroke-width="1.5"/><circle cx="15" cy="10" r="2.5" fill="none" stroke="#fff" stroke-width="1.5"/><path d="M4 28l5-6h12l5 6z" fill="none" stroke="#fff" stroke-width="1.5"/></svg>
  <span style="line-height:19px">48 Ferrow Lane&nbsp;|&nbsp;Bexwell, ON<br>&nbsp;|&nbsp;B4X 2K7</span>
</div>
<div class="abs contact-item" style="left:556px;top:3362px">
  <svg width="28" height="22" viewBox="0 0 28 22"><rect x="1" y="1" width="26" height="20" fill="none" stroke="#fff" stroke-width="1.5"/><path d="M1 1l13 11L27 1" fill="none" stroke="#fff" stroke-width="1.5"/></svg>
  <span>hello@lumbrabexwell.example</span>
</div>
<div class="abs contact-item" style="left:827px;top:3362px">
  <svg width="26" height="26" viewBox="0 0 26 26"><path d="M6 2l4 5-2 3c1 3 4 6 7 7l3-2 5 4-2 4C12 24 2 14 3 4z" fill="none" stroke="#fff" stroke-width="1.5"/></svg>
  <span>555-014-0765</span>
</div>

<!-- FOOTER -->
<div class="abs foot-col" style="left:119px;top:3468px"><h4>Dining Hours</h4><p>Courtyard is open<br>Thursday to Sunday<br>12:00pm – 9:00pm</p></div>
<div class="abs foot-col" style="left:350px;top:3468px"><h4>Canada Day Hours!</h4><p>Thursday, July 1st&nbsp; - &nbsp;Open<br>Friday, July 2nd&nbsp; - &nbsp;Open<br>Saturday, July 3rd&nbsp; - &nbsp;Open<br>Sunday, July 4th&nbsp; - &nbsp;Closed</p></div>
<div class="abs foot-col" style="left:624px;top:3468px"><h4>Takeout &amp; Kitchen Hours</h4><p>Thursday to Sunday<br>12:00pm - 8:00pm</p></div>
<div class="abs foot-col" style="left:918px;top:3468px"><h4>Outdoor Dining Hours</h4><p>Our courtyard is open!<br>Thursday to Sunday<br>12:00pm - 9:00pm</p></div>
<div class="abs foot-rule"></div>
<div class="abs copyright">Copyright © 2021 lumbrabexwell. All rights reserved.</div>

</body>
</html>
```